IT Company requires new Business Card design.

Over the years we have had a few different business card designs. We are now due for new cards across the board for all staff. We felt this would be a good time to start fresh with a new design. Our traditional card simply had our details on the front, and a list of services on the back. We don't particularly need the list of services, we have had cards where the only thing on the rear of the card was our logo.
Feel free to be creative, we would like our tag line "Complete IT Management" to appear at some point, doesn't necessarily have to be with the logo.
I have attached samples and drafts of various previous cards we have used over the years.

```html
<!DOCTYPE html>
<html lang="en">
<head>
<meta charset="utf-8">
<title>Cobalt Bay – Business Card</title>
<link href="https://fonts.googleapis.com/css2?family=PT+Sans:wght@400;700&display=swap" rel="stylesheet">
<style>
  :root {
    --bg: #e9e7e3;
    --card: #ffffff;
    --slate: #5f7282;
    --ink: #2f2f2f;
    --text-light: #ffffff;
    --muted: #555b60;
  }
  * { box-sizing: border-box; margin: 0; padding: 0; }
  html, body {
    width: 1200px; height: 720px; overflow: hidden;
    background: var(--bg);
    font-family: "PT Sans", Arial, sans-serif;
  }
  .canvas {
    position: relative; width: 1200px; height: 720px;
  }
  .card {
    position: absolute; top: 205px;
    width: 540px; height: 310px;
    background: var(--card);
    box-shadow: 0 6px 18px rgba(0,0,0,0.18);
    overflow: hidden;
  }
  .card--front { left: 40px; }
  .card--back { left: 620px; }

  .card__band { position: absolute; inset: 0; width: 540px; height: 310px; }

  .brand {
    position: absolute; display: flex; align-items: center; gap: 12px;
    color: var(--slate); font-weight: 700; text-transform: uppercase;
    line-height: 1;
  }
  .brand__mark { background: var(--slate); flex: none; }
  .card--front .brand { left: 100px; top: 38px; font-size: 46px; }
  .card--front .brand__mark { width: 42px; height: 42px; }

  .holder {
    position: absolute; left: 110px; top: 176px; width: 165px;
    text-align: right; color: var(--text-light); font-size: 14px; line-height: 1.35;
  }
  .holder__name { font-weight: 700; font-size: 17px; }
  .divider {
    position: absolute; left: 290px; top: 150px; width: 1px; height: 130px;
    background: var(--text-light);
  }
  .contacts {
    position: absolute; left: 302px; top: 148px;
    list-style: none; color: var(--text-light); font-size: 13.5px;
  }
  .contacts li { display: flex; align-items: center; gap: 8px; height: 23px; }
  .contacts svg { width: 13px; height: 13px; flex: none; }

  .card--back .brand {
    left: 0; right: 0; top: 92px; justify-content: center;
    font-size: 62px;
  }
  .card--back .brand__mark { width: 54px; height: 54px; }
  .tagline {
    position: absolute; left: 0; right: 0; top: 172px; text-align: center;
    color: var(--slate); font-size: 19px; letter-spacing: 5px; text-transform: uppercase;
  }
  .web {
    position: absolute; left: 0; right: 0; bottom: 30px; text-align: center;
    color: var(--muted); font-weight: 700; font-size: 17px; letter-spacing: 1.5px;
  }
</style>
</head>
<body>
<main class="canvas">

  <section class="card card--front" aria-label="Card front">
    <svg class="card__band" viewBox="0 0 540 310" aria-hidden="true">
      <path d="M0 226 Q270 112 540 97" fill="none" stroke="var(--ink)" stroke-width="5"/>
      <path d="M0 234 Q270 122 540 106 L540 310 L0 310 Z" fill="var(--slate)"/>
    </svg>

    <div class="brand"><span class="brand__mark"></span><span>Cobalt Bay</span></div>

    <div class="holder">
      <p class="holder__name">Daniel Reyes</p>
      <p>Operations Manager</p>
      <p>Unit 4 12 Harbour Road</p>
      <p>Kelvale WA 6000</p>
    </div>

    <span class="divider"></span>

    <ul class="contacts">
      <li>
        <svg viewBox="0 0 16 16" fill="#fff"><path d="M3 1h3l1.5 4-2 1.3a9 9 0 0 0 4.2 4.2L11 8.5l4 1.5v3a2 2 0 0 1-2 2A12 12 0 0 1 1 3a2 2 0 0 1 2-2z"/></svg>
        08 5550 1234
      </li>
      <li>
        <svg viewBox="0 0 16 16" fill="#fff"><rect x="4" y="0.5" width="8" height="15" rx="1.5"/><rect x="5.5" y="2.5" width="5" height="8" fill="var(--slate)"/></svg>
        0400 555 018
      </li>
      <li>
        <svg viewBox="0 0 16 16" fill="#fff"><rect x="4" y="1" width="8" height="5"/><rect x="1" y="6" width="14" height="7" rx="1.5"/><rect x="4" y="11" width="8" height="4"/></svg>
        08 5550 1235
      </li>
      <li>
        <svg viewBox="0 0 16 16"><rect x="1" y="3" width="14" height="10" rx="1" fill="#fff"/><path d="M1 4l7 5 7-5" fill="none" stroke="var(--slate)" stroke-width="1.5"/></svg>
        daniel@cobaltbay.com.au
      </li>
      <li>
        <svg viewBox="0 0 16 16" fill="none" stroke="#fff" stroke-width="1.4"><circle cx="8" cy="8" r="6.5"/><ellipse cx="8" cy="8" rx="3" ry="6.5"/><path d="M1.5 8h13"/></svg>
        www.cobaltbay.com.au
      </li>
    </ul>
  </section>

  <section class="card card--back" aria-label="Card back">
    <div class="brand"><span class="brand__mark"></span><span>Cobalt Bay</span></div>
    <p class="tagline">Complete IT Management</p>
    <p class="web">www.cobaltbay.com.au</p>
  </section>

</main>
</body>
</html>
```